NEW Modern Sleek Business Card for VR Language Startup

Our startup is using VR to lead the next wave of world language education. We need a two-sided business card that introduces the larger organization (Brightloom Language Inc) and our contact info on one side and shows the product, Glimwoorld, on the other side.

Side 1 (contact info)= Brightloom Logo and Contact info (name, title, phone, email)

Side 2 (product)= Glimworld logo, text, and website
Text= Culturally Immersive Language Learning Games
Website= www.glimworld-play.com

Target Market(s)

Education, Technology

Contact Information for Business Card

Contact info will be updated upon approval of the design. For now, put this as a placeholder.

Perry Dunmore
Founder & CEO
pdunmore@quillpost-mail.net
(555)-014-2286

Font styles to use
Other font styles liked:
• Gibson and Century Gothic are the brand fonts

Requirements
Nice to have
• I would love to see cohesion between the design and colors of the two logos. I have attached a few business card designs that I like, so you can get a feel for my preferred style.

```html
<!DOCTYPE html>
<html lang="en">
<head>
<meta charset="utf-8">
<title>Brightloom Language — Business Card</title>
<link rel="stylesheet" href="https://fonts.googleapis.com/css2?family=Montserrat:wght@600&family=Roboto:ital,wght@0,400;0,500;1,400&display=swap">
<style>
  :root {
    --backdrop: #dcdde0;
    --card: #ffffff;
    --ink: #1c1c1f;
    --ink-soft: #3a3a3f;
    --name-blue: #3a8ff0;
    --title-orange: #ff6a2a;
    --line-blue: #4f6df5;
    --grad-cyan: #19e3e8;
    --grad-blue: #5a6cf2;
    --grad-violet: #9a4be8;
    --grad-red: #ff3a4a;
    --grad-amber: #f7a33a;
  }
  * { box-sizing: border-box; margin: 0; padding: 0; }
  html, body { width: 1200px; height: 800px; overflow: hidden; }
  body {
    background: var(--backdrop);
    display: flex;
    align-items: center;
    justify-content: center;
    gap: 40px;
    font-family: "Roboto", Arial, sans-serif;
    color: var(--ink);
  }
  .card {
    position: relative;
    width: 540px;
    height: 309px;
    background: var(--card);
    box-shadow: 0 6px 18px rgba(0,0,0,0.12);
    overflow: hidden;
  }

  /* Contact side */
  .wordmark {
    font-family: "Montserrat", "Century Gothic", sans-serif;
    font-weight: 600;
    color: var(--ink);
    letter-spacing: 0.12em;
    text-transform: uppercase;
    display: flex;
    align-items: center;
    gap: 10px;
  }
  .wordmark-dot {
    width: 14px; height: 14px; border-radius: 50%;
    background: var(--grad-blue);
  }
  .contact .wordmark { position: absolute; left: 36px; top: 36px; font-size: 26px; }
  .person { position: absolute; left: 36px; top: 120px; }
  .person-name { font-size: 24px; font-weight: 500; color: var(--name-blue); line-height: 1.1; }
  .person-title { font-size: 15px; color: var(--title-orange); margin-top: 2px; }
  .contact-list { list-style: none; margin-top: 16px; font-size: 13px; color: var(--ink-soft); }
  .contact-list li { display: flex; align-items: center; gap: 8px; margin-bottom: 6px; }
  .contact-list svg { width: 12px; height: 12px; fill: var(--ink); }
  .brand-visual {
    position: absolute;
    right: 40px; top: 60px;
    width: 210px; height: 210px;
    border-radius: 50%;
    background: linear-gradient(200deg, var(--grad-amber) 0%, var(--grad-red) 30%, var(--grad-violet) 55%, var(--grad-blue) 75%, var(--grad-cyan) 100%);
  }

  /* Product side */
  .product .product-mark {
    position: absolute; left: 70px; top: 70px;
    font-size: 36px; letter-spacing: 0.01em; text-transform: none;
    color: var(--grad-blue);
  }
  .product .product-mark .wordmark-dot { width: 22px; height: 22px; background: var(--grad-cyan); }
  .product .parent-mark {
    position: absolute; right: 60px; top: 140px; font-size: 22px;
  }
  .product .parent-mark .wordmark-dot { background: var(--grad-red); }
  .tagline {
    position: absolute; left: 70px; top: 200px;
    font-size: 15px; font-style: italic; color: var(--ink-soft);
  }
  .web-rule {
    position: absolute; left: 40px; right: 40px; top: 238px;
    display: flex; align-items: center; gap: 10px;
  }
  .rule { flex: 1; height: 1px; background: linear-gradient(90deg, transparent, var(--line-blue)); }
  .rule.end { background: linear-gradient(90deg, var(--line-blue), transparent); }
  .node { width: 8px; height: 8px; border-radius: 50%; border: 1.5px solid var(--line-blue); }
  .website { font-size: 15px; color: var(--line-blue); }
</style>
</head>
<body>
  <section class="card contact" aria-label="Contact side">
    <div class="wordmark"><span class="wordmark-dot"></span>Brightloom</div>
    <div class="person">
      <p class="person-name">Perry Dunmore</p>
      <p class="person-title">Founder &amp; CEO</p>
      <ul class="contact-list">
        <li><svg viewBox="0 0 24 24" aria-hidden="true"><path d="M6.6 10.8a15 15 0 0 0 6.6 6.6l2.2-2.2a1 1 0 0 1 1-.25 11.4 11.4 0 0 0 3.6.57 1 1 0 0 1 1 1V20a1 1 0 0 1-1 1A17 17 0 0 1 3 4a1 1 0 0 1 1-1h3.5a1 1 0 0 1 1 1c0 1.25.2 2.45.57 3.6a1 1 0 0 1-.25 1z"/></svg>(555)-014-2286</li>
        <li><svg viewBox="0 0 24 24" aria-hidden="true"><path d="M2 5h20v14H2zm2 2v.5l8 5 8-5V7l-8 5z"/></svg>pdunmore@quillpost-mail.net</li>
      </ul>
    </div>
    <div class="brand-visual" role="img" aria-label="Large colourful brand graphic in amber, red, violet, blue and cyan"></div>
  </section>

  <section class="card product" aria-label="Product side">
    <div class="wordmark product-mark"><span class="wordmark-dot"></span>Glimworld</div>
    <div class="wordmark parent-mark"><span class="wordmark-dot"></span>Brightloom</div>
    <p class="tagline">Culturally Immersive Language Learning Games</p>
    <div class="web-rule">
      <span class="rule"></span><span class="node"></span>
      <span class="website">www.glimworld-play.com</span>
      <span class="node"></span><span class="rule end"></span>
    </div>
  </section>
</body>
</html>
```